Sickle Cell Patient Flyer

I need this be appealing to families dealing with sickle cell disease. Both informative-introducing the idea that a stroke prevention program is not only easy for their children but necessary. Stroke is a risk to all with children with SCD.
I included a few info flyers from the Vessel Alliance and licensed to me photos I like. I am open to suggestions.
web address is brightpathwellbeing.net
Call to schedule 833-412-7086
TCD is a safe and accurate tool that makes stroke prevention possible for your SCD patients and family.
Risk is highest for SCD sufferers age 2 to 5. Protect your childs future.

Target Market(s)

Parents, families and medical professionals

Industry/Entity Type

Medical wellness

Font styles to use
Other font styles liked:
• something close to my logo font

Colors
0094D4
00A9DD
6FCCEA
C7EBF8
E9F6FB

Requirements
Nice to have
• pictures of kids (Children of color) pictures of Brains, kids happy with medical professionals
Should not have
• dark colors

```html
<!DOCTYPE html>
<html lang="en">
<head>
<meta charset="utf-8">
<title>Stroke Prevention for Children with Sickle Cell Disease</title>
<link href="https://fonts.googleapis.com/css2?family=Poppins:wght@400;500;600;700;800&family=Berkshire+Swash&display=swap" rel="stylesheet">
<style>
:root{
  --navy:#14306f;
  --navy-deep:#0b1b55;
  --hero-top:#1f4596;
  --mint:#86d6b0;
  --mint-text:#7fd3aa;
  --sky:#3fb0e6;
  --sky-soft:#6fccea;
  --ink:#1b2350;
  --footer-blue:#1d4e95;
  --footer-grey:#4a4a4a;
  --page:#eef1f4;
  --white:#ffffff;
}
*{margin:0;padding:0;box-sizing:border-box}
html,body{width:1200px;height:2836px;overflow:hidden;background:var(--page)}
body{font-family:'Poppins',sans-serif;color:var(--ink)}
h1{font-size:inherit;font-weight:inherit}
.flyer{position:absolute;left:0;top:642px;width:1200px;height:1553px;background:var(--white);overflow:hidden;box-shadow:0 10px 40px rgba(0,0,0,.12)}
.abs{position:absolute;white-space:nowrap}
.hero{left:0;top:0;width:1200px;height:619px;background:linear-gradient(135deg,var(--hero-top) 0%,#142f7a 50%,var(--navy-deep) 100%)}
.brand{left:60px;top:80px;display:flex;align-items:center;gap:18px;font-weight:700;font-size:52px;line-height:1.1;color:var(--mint)}
.brand-mark{width:44px;height:44px;background:var(--mint)}
.headline-top{left:56px;top:296px;font-weight:800;font-size:54px;line-height:1.1;color:var(--mint-text);letter-spacing:.5px}
.headline-main{left:52px;top:362px;font-family:'Berkshire Swash',serif;font-size:94px;line-height:1;color:var(--white)}
.headline-sub{left:56px;top:482px;font-weight:800;font-size:50px;line-height:1.05;color:var(--sky)}
.hero-photo{left:600px;top:14px;width:600px;height:605px;background:radial-gradient(circle at 55% 45%,#3a4b7a 0%,#1a2a66 55%,transparent 80%)}
.banner{left:76px;top:619px;width:1046px;height:88px;background:var(--mint);border-radius:0 0 28px 28px;display:flex;align-items:center;justify-content:center;font-weight:700;font-size:42px;color:var(--ink)}
.info{left:107px;top:736px;width:986px;height:322px;border:2px solid var(--sky-soft)}
.info-art{left:107px;top:736px;width:395px;height:322px;background:radial-gradient(circle at 40% 45%,#2f6fd0 0%,#1d3f9c 60%,#14296e 100%)}
.icon{width:78px;height:78px;border-radius:50%;background:var(--sky);border:5px solid #d6eefa;display:flex;align-items:center;justify-content:center}
.info-text{left:568px;width:500px;font-size:25px;line-height:29px;color:#333a55;white-space:normal}
.stat{left:0;width:1200px;text-align:center;font-weight:600;font-size:30px;color:#333a55}
.stat b{font-weight:700;color:var(--navy)}
.pct{display:inline-block;width:58px;height:58px;line-height:58px;border-radius:50%;background:var(--navy);color:var(--white);font-size:26px;vertical-align:middle;text-align:center}
.pill{display:inline-block;padding:2px 22px;border-radius:8px;background:var(--navy);color:var(--white);font-weight:600;margin-left:16px}
.note{left:212px;top:1215px;width:870px;height:94px;background:var(--mint);border-radius:0 22px 22px 0;padding:12px 18px 0 50px;color:var(--white);font-weight:500;font-size:26px;line-height:1.25;white-space:normal}
.note-icon{left:125px;top:1206px;width:112px;height:112px;border-radius:50%;background:var(--sky);border:6px solid #d6eefa;display:flex;align-items:center;justify-content:center}
.cta{left:0;width:1200px;top:1324px;text-align:center;font-weight:800;font-size:52px;line-height:1.2;color:var(--navy)}
.cta span{color:var(--sky)}
.footer-label{left:84px;top:1424px;font-size:40px;line-height:1.2;font-weight:500;color:var(--sky-soft)}
.footer-phone{left:78px;top:1474px;font-size:42px;line-height:1.2;font-weight:700;color:var(--white);display:flex;align-items:center;gap:8px}
.footer-url{left:569px;top:1467px;font-size:34px;line-height:1.2;font-weight:600;color:var(--white);letter-spacing:1px}
</style>
</head>
<body>
<main class="flyer">
  <section class="abs hero"></section>
  <div class="abs hero-photo" role="img" aria-label="Smiling child in white shirt and tie pointing up at glowing and colourful brain graphics"></div>
  <div class="abs brand"><span class="brand-mark"></span><span>BrightPath<br>Wellbeing</span></div>
  <h1>
    <span class="abs headline-top">STROKE PREVENTION</span>
    <span class="abs headline-main">FOR CHILDREN</span>
    <span class="abs headline-sub">WITH SICKLE CELL<br>DISEASE IS POSSIBLE!</span>
  </h1>

  <div class="abs banner">Stroke is a risk to all with children with SCD</div>

  <div class="abs info"></div>
  <div class="abs info-art" role="img" aria-label="Silhouette of a child's head with a glowing network brain"></div>

  <div class="abs icon" style="left:463px;top:756px">
    <svg width="40" height="40" viewBox="0 0 40 40" fill="none" stroke="#fff" stroke-width="2.5"><rect x="5" y="8" width="22" height="16" rx="2"/><path d="M12 30h10M17 24v6M32 8v18"/><circle cx="32" cy="7" r="3"/></svg>
  </div>
  <div class="abs icon" style="left:463px;top:856px">
    <svg width="40" height="40" viewBox="0 0 40 40" fill="none" stroke="#fff" stroke-width="2.5"><path d="M12 34v-8c-4-3-5-8-3-13 3-6 13-7 18-2 3 3 4 7 3 11l3 4h-4v5h-6v3"/></svg>
  </div>
  <div class="abs icon" style="left:463px;top:963px">
    <svg width="40" height="40" viewBox="0 0 40 40" fill="none" stroke="#fff" stroke-width="2.5"><rect x="6" y="6" width="18" height="28" rx="2"/><path d="M10 12h10M10 20h2M14 20h2M18 20h2M10 26h2M14 26h2M30 8v14M27 22h6v8h-6z"/></svg>
  </div>
  <p class="abs info-text" style="top:770px;width:440px">Simple and painless screening for your child.</p>
  <p class="abs info-text" style="top:869px;width:470px">Our Screening uses ultrasound which is transcranial doppler.</p>
  <p class="abs info-text" style="top:958px">TCD is a safe and accurate tool that makes stroke prevention possible for your SCD patients and family.</p>

  <p class="abs stat" style="top:1082px">About <span class="pct">11%</span> of SCD patients have strokes before <b>AGE 20</b></p>
  <p class="abs stat" style="top:1144px">with The highest risk between <span class="pill">age 2 and 5</span></p>

  <div class="abs note">Screening or early signs of stroke can be a tool to for early diagnosis allowing for treatments that eliminate the risk.</div>
  <div class="abs note-icon">
    <svg width="56" height="56" viewBox="0 0 56 56" fill="none" stroke="#fff" stroke-width="3"><rect x="10" y="10" width="28" height="38" rx="3"/><path d="M18 8h12v6H18zM16 24l4 4 6-8M16 36h10"/><circle cx="38" cy="38" r="7"/><path d="M43 43l6 6"/></svg>
  </div>

  <p class="abs cta"><span>PROTECT YOUR</span> CHILDS FUTURE!</p>

  <svg class="abs" style="left:0;top:1413px" width="1200" height="140" viewBox="0 0 1200 140">
    <rect x="500" y="36" width="700" height="104" fill="#4a4a4a"/>
    <path d="M0 0H470C520 0 540 40 548 140H0Z" fill="#1d4e95"/>
  </svg>
  <p class="abs footer-label">Call to schedule</p>
  <p class="abs footer-phone">
    <svg width="30" height="30" viewBox="0 0 24 24" fill="#fff"><path d="M6.6 10.8a15 15 0 006.6 6.6l2.2-2.2a1 1 0 011-.25 11.4 11.4 0 003.6.57 1 1 0 011 1V20a1 1 0 01-1 1A17 17 0 013 4a1 1 0 011-1h3.5a1 1 0 011 1c0 1.25.2 2.45.57 3.6a1 1 0 01-.25 1z"/></svg>
    833-412-7086
  </p>
  <p class="abs footer-url">www.brightpathwellbeing.net</p>
</main>
</body>
</html>
```